Dew and Willow med spa needs an awesome eye catching billboard ad

We need a billboard ad design for a Med Spa with location sin Davenport and Windermere FL A medical spa where the beauty of nature meets the power of science to treat the whole person, mind, body and soul.

Marigold Radiance Med Spa is a medical spa where the beauty of nature meets the power of science to create gorgeous, youthful looking skin. Located in Davenport, Florida, but also serving Four Corners, Celebration, and Windermere, Florida, the talented professional team brings decades of experience in world-class skin care to provide holistic, science-backed aesthetic services and health coaching.

Industry/Entity Type

Spa

Colors
fbee3e
fece3e
eea4c8
e667a6
fbee3d

Requirements
Must have
• Locations in Davenport and Dr Phillips
Phone 407-555-0148
website www.dewandwillow-example.com

Boards for each:
Aesthetic Treatments
Cosmetic Injectables
Quoria facial
add color vs too many earthtones, to catch the eye perhaps using yellow, something that catches the eye and stands out from the normal everyday
Thank you!!!!
Nice to have
• Boards for each:
Aesthetic Treatments
Cosmetic Injectables
Quoria facial
add color vs too many earthtones, to catch the eye
photos that match services,
Thank you!!!!

```html
<!DOCTYPE html>
<html lang="en">
<head>
<meta charset="UTF-8">
<title>Cosmetic Injectables – Marigold Radiance Med Spa</title>
<link rel="stylesheet" href="https://fonts.googleapis.com/css2?family=Marcellus&family=Didact+Gothic&family=Open+Sans:wght@700;800&display=swap">
<style>
  :root {
    --bg-top: #eef3f0;
    --bg-bottom: #e3ece8;
    --slate: #5f8797;
    --band: #62899a;
    --pink: #ec8bbd;
    --gold: #c9b07f;
    --sun: #fbee3e;
    --marigold: #fece3e;
    --white: #ffffff;
    --skin-light: #f4e3dc;
    --skin-mid: #e9cfc4;
  }
  html, body {
    margin: 0;
    padding: 0;
    overflow: hidden;
    background: var(--bg-top);
  }
  .billboard {
    position: relative;
    width: 1200px;
    height: 411px;
    overflow: hidden;
    background: linear-gradient(180deg, var(--bg-top), var(--bg-bottom));
  }
  .headline {
    position: absolute;
    left: 44px;
    top: 10px;
    margin: 0;
    font-family: "Marcellus", serif;
    font-weight: 400;
    font-size: 82px;
    line-height: 1;
    color: var(--slate);
    -webkit-text-stroke: 1.6px var(--slate);
    letter-spacing: 0.5px;
    white-space: nowrap;
  }
  .treatments {
    position: absolute;
    left: 0;
    width: 862px;
    top: 96px;
    margin: 0;
    padding: 0;
    list-style: none;
    font-family: "Didact Gothic", sans-serif;
    font-size: 57px;
    line-height: 47px;
    color: var(--pink);
    text-align: center;
    white-space: nowrap;
  }
  .treatments .dot {
    display: inline-block;
    width: 18px;
    height: 18px;
    margin: 0 6px 8px;
    border-radius: 50%;
    background: var(--slate);
    vertical-align: middle;
  }
  .brand {
    position: absolute;
    left: 150px;
    top: 250px;
    display: flex;
    align-items: center;
    gap: 20px;
  }
  .brand-mark {
    flex: none;
    width: 40px;
    height: 40px;
    border-radius: 50%;
    background: var(--marigold);
  }
  .brand-text {
    display: flex;
    flex-direction: column;
    gap: 6px;
  }
  .brand-name {
    margin: 0;
    font-family: "Marcellus", serif;
    font-size: 32px;
    line-height: 1;
    letter-spacing: 5px;
    text-transform: uppercase;
    color: var(--gold);
    white-space: nowrap;
  }
  .locations {
    margin: 0;
    font-family: "Didact Gothic", sans-serif;
    font-size: 20px;
    line-height: 1;
    letter-spacing: 4px;
    text-transform: uppercase;
    color: var(--slate);
    white-space: nowrap;
  }
  .locations .dot {
    display: inline-block;
    width: 8px;
    height: 8px;
    margin: 0 8px 3px;
    border-radius: 50%;
    background: var(--marigold);
    vertical-align: middle;
  }
  .portrait {
    position: absolute;
    right: 0;
    top: 0;
    width: 380px;
    height: 353px;
    background:
      radial-gradient(ellipse 55% 70% at 62% 45%, var(--skin-light) 0%, var(--skin-mid) 60%, rgba(233,207,196,0) 100%),
      linear-gradient(90deg, rgba(238,243,240,0) 0%, rgba(201,165,138,0.25) 100%);
  }
  .accent-rule {
    position: absolute;
    left: 0;
    bottom: 52px;
    width: 1200px;
    height: 6px;
    background: linear-gradient(90deg, var(--sun), var(--marigold));
  }
  .contact-band {
    position: absolute;
    left: 0;
    bottom: 0;
    width: 1200px;
    height: 52px;
    background: var(--band);
    display: flex;
    align-items: center;
    justify-content: center;
  }
  .contact {
    margin: 0;
    font-family: "Open Sans", sans-serif;
    font-weight: 800;
    font-size: 31px;
    color: var(--white);
    white-space: nowrap;
    transform: translateX(20px);
  }
  .contact .sep {
    color: var(--sun);
  }
</style>
</head>
<body>
  <main class="billboard">
    <h1 class="headline">Cosmetic Injectables</h1>
    <ul class="treatments">
      <li>Frown lines<span class="dot"></span>Forehead lines</li>
      <li>Crow’s feet<span class="dot"></span>Bunny lines</li>
    </ul>
    <div class="brand">
      <span class="brand-mark"></span>
      <div class="brand-text">
        <p class="brand-name">Marigold Radiance Med Spa</p>
        <p class="locations">Davenport<span class="dot"></span>Dr Phillips</p>
      </div>
    </div>
    <div class="portrait" role="img" aria-label="Portrait photo of a woman with smooth skin touching her cheek"></div>
    <div class="accent-rule"></div>
    <footer class="contact-band">
      <p class="contact">407-555-0148 <span class="sep">|</span> www.dewandwillow-example.com</p>
    </footer>
  </main>
</body>
</html>
```